Business Card - high end, modern health care

Hey designers!

We need a double sided business card for the boutique, cutting edge physical therapy rehabilitation centre in Sydney's Northern Beaches.

With the most qualified physios in the area The Harbourview Motion Clinic does what other physiotherapy practices do not, we take our time with our patients giving them longer appointments, better physios and therefor faster results!

We guarantee that the service people receive at THMC will be unparalleled.

Hence we need a business card to reflect our modern, boutique, high end service. The final design needs to reflect that we are in a class of our own yet with the feel of beachside retreat.

Below I have attached our logo in both blue on white and white on blue. The exact colour is;
and the font that we have used in our logo is Tex Gyre Aventador.

I like the idea of the blue as the main colour as it is more eye catching and our signage onto the main road will be in this blue and in the interest of consistency across marketing the blue needs to be a part of the design. However I would appreciate a few designs onto a wooden background as this is a visual theme within the fitout of the practice.

The design needs to be of standard size (91x55mm).

Target Market(s)

We target people who have an end outcome in mind and those who have had poor experiences with other providers and ensure that everyone gets the care that they deserve with a premium service that is tailored to the individuals circumstances. As a premium service, the target market is highly educated, business and tech savvy with the additional target market of elderly people who have self funded their retirement and see value in paying for the best ongoing rehabilitation to maintain independence.

Industry/Entity Type

Physical Therapy

Contact Information for Business Card

Name, designation( Titled Musculoskeletal Physiotherapist... there will also be those in the company that have multiple designations ie 5 or 6 words long), phone number, email, facebook, instagram, address

Font styles to use
Sans Serif

Colors

Designer to choose colors to be used in the design.

Requirements
Must have
• Front - The logo as large as possible, blue or wooden theme, and all of the important details.
• Back - A blank space/lines on which to write appointment times (no "Appointment, date, time" etc.)
Nice to have
• facebook url
• logos for facebook and instagram
• Mini logos for the phone and email?

```html
<!DOCTYPE html>
<html lang="en">
<head>
<meta charset="utf-8">
<title>The Harbourview Motion Clinic – Business Card</title>
<link href="https://fonts.googleapis.com/css2?family=Raleway:wght@300;400&display=swap" rel="stylesheet">
<style>
  :root{
    --brand-blue:#0b4a93;
    --paper:#f2f2f2;
    --ink:#1a1a1a;
    --rule:#2a2a2a;
    --backdrop:#cfcfcf;
    --social-fb:#1d8fd6;
    --social-ig:#e0588f;
  }
  *{box-sizing:border-box;margin:0;padding:0}
  html,body{width:1200px;height:960px;overflow:hidden}
  body{background:var(--backdrop);position:relative;font-family:"Raleway",sans-serif;color:var(--ink)}
  .card{position:absolute;width:680px;height:411px;background:var(--paper);box-shadow:0 4px 14px rgba(0,0,0,.18);overflow:hidden}
  .card--brand{left:460px;top:40px}
  .card--contact{left:60px;top:505px}

  /* brand side */
  .brand-field{position:absolute;inset:0}
  .brand-name{position:absolute;display:flex;align-items:center;gap:14px;color:var(--brand-blue);font-family:"Raleway",sans-serif;font-weight:400;white-space:nowrap}
  .brand-name__dot{border-radius:50%;background:var(--brand-blue);flex:none}
  .brand-name__text{line-height:1.15}
  .card--brand .brand-name{left:335px;top:200px;font-size:27px}
  .card--brand .brand-name__dot{width:44px;height:44px}

  /* contact side */
  .logo-column{position:absolute;left:0;top:0;width:130px;height:100%;border-right:1.5px solid var(--rule)}
  .logo-column .brand-name{left:50%;top:50%;transform:translate(-50%,-50%) rotate(-90deg);font-size:21px;gap:12px}
  .logo-column .brand-name__dot{width:34px;height:34px}

  .person{position:absolute;left:160px;top:52px}
  .person-name{font-size:34px;font-weight:300;letter-spacing:.3px}
  .person-name .accent{color:var(--brand-blue)}
  .person-role{font-size:14px;margin-top:4px}
  .rule{position:absolute;left:130px;right:0;height:0;border-top:1.5px solid var(--rule)}
  .rule--top{top:140px}
  .rule--bottom{top:296px}
  .write-line{position:absolute;left:150px;right:40px;top:366px;border-top:1.5px dashed #555}

  .contact-list{position:absolute;left:150px;top:160px;list-style:none;font-size:17px}
  .contact-list li{display:flex;align-items:center;gap:12px;height:38px}
  .icon{width:22px;height:22px;flex:none}
  .social-dot{width:22px;height:22px;border-radius:50%;flex:none}
  .social-dot--fb{background:var(--social-fb)}
  .social-dot--ig{background:var(--social-ig)}
  .social-ig{position:absolute;left:430px;top:246px;display:flex;align-items:center;gap:12px;font-size:17px}
</style>
</head>
<body>

<section class="card card--brand" aria-label="Card brand side">
  <svg class="brand-field" viewBox="0 0 680 411" width="680" height="411">
    <rect width="680" height="411" fill="var(--brand-blue)"/>
    <circle cx="750" cy="230" r="480" fill="var(--paper)"/>
    <circle cx="165" cy="160" r="92" fill="var(--paper)" role="img" aria-label="Large brand emblem area"/>
  </svg>
  <div class="brand-name">
    <span class="brand-name__dot"></span>
    <span class="brand-name__text">The Harbourview<br>Motion Clinic</span>
  </div>
</section>

<section class="card card--contact" aria-label="Card contact side">
  <div class="logo-column">
    <div class="brand-name">
      <span class="brand-name__dot"></span>
      <span class="brand-name__text">The Harbourview<br>Motion Clinic</span>
    </div>
  </div>

  <div class="person">
    <p class="person-name">Name of <span class="accent">Person</span></p>
    <p class="person-role">Designation</p>
  </div>
  <div class="rule rule--top"></div>

  <ul class="contact-list">
    <li>
      <svg class="icon" viewBox="0 0 24 24" aria-hidden="true"><circle cx="12" cy="12" r="10.5" fill="none" stroke="#111" stroke-width="1.6"/><path d="M9 7.5c-1.2.6-1.5 2-1 3.6.8 2.4 2.5 4.2 4.6 5.2 1.3.6 2.6.3 3.2-.8l-1.8-1.6-1.3.8c-1.1-.6-2-1.6-2.5-2.8l.9-1.1L9 7.5z" fill="#111"/></svg>
      <span>555.014.2290</span>
    </li>
    <li>
      <svg class="icon" viewBox="0 0 24 24" aria-hidden="true"><rect x="2" y="5" width="20" height="14" fill="#111"/><path d="M2 5l10 8 10-8" fill="none" stroke="#fff" stroke-width="1.4"/></svg>
      <span>clinicname@email.com</span>
    </li>
    <li>
      <span class="social-dot social-dot--fb"></span>
      <span>facebook/name</span>
    </li>
  </ul>
  <div class="social-ig">
    <span class="social-dot social-dot--ig"></span>
    <span>instagram_name</span>
  </div>

  <div class="rule rule--bottom"></div>
  <div class="write-line"></div>
</section>

</body>
</html>
```